Flyer-Design für Vegane und Gluten freie Haarpflege
Zielgruppe
Herstellung + Vertrieb von VEGANEN Haarpflegeprodukten
Shampoo, Conditioner Gluten frei und Vegan nicht an Tieren getestet und biologisch abbaubar
Aufgabenstellung
DIN 4 Grösse 2 Seiten Produktinformation für Verbraucher

```html
<!DOCTYPE html>
<html lang="de">
<head>
<meta charset="utf-8">
<title>Terra Pura – Produktinformation</title>
<link rel="stylesheet" href="https://fonts.googleapis.com/css2?family=Questrial&family=Roboto+Condensed:wght@300;400&family=Tinos:ital@1&display=swap">
<style>
  :root {
    --ink: #111111;
    --white: #ffffff;
    --amber: #f7af00;
    --grey: #4a4a4a;
    --photo-black: #0b0805;
    --photo-brown: #3b2409;
    --photo-gold: #b5761a;
    --photo-light: #ecc77a;
    --bottle: #f4f4f4;
    --bottle-shade: #cfcfcf;
    --bottle-edge: #b9b9b9;
  }
  * { margin: 0; padding: 0; box-sizing: border-box; }
  html, body { width: 848px; height: 1200px; overflow: hidden; background: var(--white); }
  .flyer { position: relative; width: 848px; height: 1200px; overflow: hidden; background: var(--white); }

  .hero {
    position: absolute; left: 0; top: 0; width: 848px; height: 517px; overflow: hidden;
    background:
      radial-gradient(ellipse 38% 45% at 76% 55%, var(--photo-light) 0%, rgba(216,160,72,0.7) 45%, transparent 75%),
      radial-gradient(ellipse 30% 40% at 14% 62%, var(--photo-black) 0%, rgba(30,18,8,0.85) 55%, transparent 90%),
      radial-gradient(ellipse 75% 60% at 55% 72%, var(--photo-gold) 0%, #8a5614 45%, var(--photo-brown) 80%),
      var(--photo-black);
  }
  .hero::before {
    content: ""; position: absolute; left: -10%; top: -62%; width: 130%; height: 90%;
    border-radius: 50%; background: linear-gradient(180deg, var(--photo-black) 60%, rgba(11,8,5,0.85) 100%);
  }
  .hero-quote {
    position: absolute; left: 46px; top: 398px; width: 516px;
    font-family: "Tinos", "Times New Roman", serif; font-style: italic;
    font-size: 25px; line-height: 26.6px; text-align: center; white-space: nowrap;
    text-transform: uppercase; color: var(--white); letter-spacing: -0.9px;
  }

  .title {
    position: absolute; left: 58px; top: 550px;
    font-family: "Questrial", Arial, sans-serif; font-weight: 400;
    font-size: 53px; letter-spacing: 1.5px; color: var(--ink); line-height: 1;
  }
  .claim-band {
    position: absolute; left: 0; top: 606px; width: 496px; height: 63px;
    background: var(--amber);
  }
  .claim {
    position: absolute; left: 60px; top: 2px;
    font-family: "Questrial", Arial, sans-serif;
    font-size: 24.5px; line-height: 30px; color: var(--white); letter-spacing: 0.9px;
  }

  .body-copy {
    position: absolute; left: 59px; top: 714px; width: 438px;
    font-family: "Roboto Condensed", Arial, sans-serif; font-weight: 300;
    font-size: 16px; line-height: 24.2px; text-align: justify; hyphens: auto;
    text-transform: uppercase; color: var(--ink);
  }

  .signature {
    position: absolute; left: 61px; top: 1110px;
    font-family: "Questrial", Arial, sans-serif;
    font-size: 24px; letter-spacing: 3px; color: var(--grey);
  }

  .bottle {
    position: absolute; top: 677px; width: 115px; height: 486px;
    border-radius: 8px / 6px;
    box-shadow: inset 0 0 0 1px rgba(0,0,0,0.06);
    background:
      linear-gradient(180deg, transparent 94px, rgba(0,0,0,0.08) 95px, rgba(255,255,255,0.6) 97px, transparent 100px),
      linear-gradient(90deg, var(--bottle-edge) 0%, var(--bottle-shade) 6%, var(--bottle) 28%, var(--white) 55%, var(--bottle) 80%, var(--bottle-shade) 95%, var(--bottle-edge) 100%);
  }
  .bottle-left { left: 547px; }
  .bottle-right { left: 685px; }
</style>
</head>
<body>
<main class="flyer">
  <section class="hero" role="img" aria-label="Foto: Frau mit langen blonden Locken liegt auf goldenem Stoff">
    <p class="hero-quote">“Terra Pura Balance ist gluten frei<br>und vegan, nicht an Tieren getestet<br>und biologisch abbaubar”</p>
  </section>

  <h1 class="title">TERRA PURA</h1>
  <div class="claim-band">
    <p class="claim">MIT EDLEN ROHSTOFFEN<br>AUS NACHHALTIGEN RESSOURCEN</p>
  </div>

  <p class="body-copy">Es ist ganz einfach, um Säure auszugleichen braucht man Base. Um Base zu neutralisieren benötigt man Säure. Daher muss man vor und nach dem Haare waschen immer einen pH-Ausgleich machen. Der Balancer ist ein Muss vor und nach jeglicher Kopf- und Haarwäsche um die Kopfhaut zu neutralisieren müssen Shampoos entweder etwas saurer oder basischer eingestellt sein, somit kann die Kopfhaut schon während der Reinigung auf den neutralen pH-Wert zurückgeführt werden.</p>

  <p class="signature">LORENZ ALBRECHT</p>

  <div class="bottle bottle-left" role="img" aria-label="Produktfoto: weiße Shampooflasche"></div>
  <div class="bottle bottle-right" role="img" aria-label="Produktfoto: weiße Shampooflasche"></div>
</main>
</body>
</html>
```